bail bonds business

Need a web design for a Bail Bond company. At Fernlow Bails, we specialize in getting arrested defendants out of jail. Also, I have all the necessary information already uploaded in the files.

Target Market(s)

Arrested defendants and their families who will post bails on their behalf.

Industry/Entity Type

Business

Coding

Coded - Design and coding required

Number of Pages Required

1 page

```html
<!DOCTYPE html>
<html lang="en">
<head>
<meta charset="utf-8">
<title>Fernlow Bails Inc</title>
<link rel="stylesheet" href="https://fonts.googleapis.com/css2?family=Open+Sans:wght@300;400;600;700&display=swap">
<style>
:root{
  --red:#c8102e;
  --red-dark:#9e0c22;
  --red-deep:#8a0a1d;
  --ink:#333333;
  --muted:#777777;
  --line:#e2e2e2;
  --white:#ffffff;
  --night:#141414;
}
*{margin:0;padding:0;box-sizing:border-box}
html,body{width:1200px;height:2508px;overflow:hidden}
body{font-family:"Open Sans",Arial,sans-serif;color:var(--ink);background:var(--white);position:relative}
.site-header{height:64px;display:flex;align-items:center;justify-content:space-between;padding:0 48px 0 56px;background:var(--white)}
.brand{display:flex;align-items:center;gap:10px;font-weight:700;font-size:17px;color:var(--ink)}
.brand-mark{width:34px;height:34px;border-radius:50%;background:var(--red)}
.main-nav{display:flex;gap:44px}
.main-nav a{font-size:12px;font-weight:600;color:var(--ink);text-decoration:none;letter-spacing:.5px}
.main-nav a.active{color:var(--red);border-bottom:2px solid var(--red);padding-bottom:4px}
.hero{position:relative;height:584px;background:radial-gradient(ellipse at 25% 40%,#4a4440 0%,#26211f 45%,#0e0c0c 100%)}
.hero-text{position:absolute;right:96px;top:206px;text-align:right;color:var(--white)}
.hero-text h2{font-size:29px;font-weight:700;letter-spacing:3px;margin-bottom:24px}
.hero-text p{font-size:19px;font-weight:400;letter-spacing:1.5px;line-height:42px}
.slider-controls{position:absolute;left:50%;transform:translateX(-50%);bottom:-28px;display:flex;gap:28px;background:var(--white);padding:10px 26px;border-radius:40px 40px 0 0}
.slider-btn{width:40px;height:40px;border:1px solid #bdbdbd;border-radius:50%;display:flex;align-items:center;justify-content:center}
.section-title{text-align:center;font-size:30px;font-weight:400;letter-spacing:1.5px;color:var(--ink)}
.title-rule{width:60px;height:2px;background:var(--red);margin:14px auto 0}
.about{padding:74px 140px 0;text-align:center;height:968px - 648px}
.about-lead{color:var(--red);font-size:15px;margin-top:36px}
.about-body{color:var(--muted);font-size:12.5px;line-height:22px;margin:22px auto 0;max-width:900px}
.btn{display:inline-block;background:var(--red);color:var(--white);font-weight:600;font-size:13px;letter-spacing:1px;text-decoration:none}
.about .btn{margin-top:34px;padding:12px 22px}
.divider{position:absolute;left:0;right:0;top:1032px;border-top:1px solid var(--line)}
.offer{position:absolute;top:1064px;left:0;right:0;text-align:center}
.offer-intro{font-size:13px;color:var(--muted);margin-top:40px}
.offer-list{display:flex;justify-content:center;gap:58px;margin-top:60px;list-style:none}
.offer-item{width:160px;display:flex;flex-direction:column;align-items:center}
.offer-icon{width:150px;height:150px;border-radius:50%;border:1px solid var(--line);box-shadow:0 4px 14px rgba(0,0,0,.08);display:flex;align-items:center;justify-content:center}
.offer-label{margin-top:24px;color:var(--red);font-size:12px;font-weight:700;letter-spacing:.5px}
.offer .btn{margin-top:64px;padding:16px 30px;font-size:14px}
.service-area{position:absolute;top:1600px;left:0;width:1200px;height:592px;background:radial-gradient(ellipse at 50% 35%,#4a4646 0%,#232121 45%,#0b0b0b 100%);text-align:center;color:var(--white)}
.service-area .section-title{color:var(--white);margin-top:60px}
.service-area .title-rule{background:var(--white);opacity:.6}
.service-text{font-size:33px;font-weight:300;letter-spacing:3px;line-height:60px;margin-top:140px}
.site-footer{position:absolute;top:2192px;left:0;width:1200px;height:268px;background:linear-gradient(180deg,var(--red) 0%,var(--red-dark) 100%);color:var(--white);display:flex;padding:18px 0 0 100px}
.footer-col h4{font-size:12px;font-weight:700;letter-spacing:.5px;margin-bottom:12px}
.footer-col ul{list-style:none}
.footer-col li{font-size:11.5px;line-height:22px}
.col-links{width:180px}
.col-news{width:320px}
.col-follow{width:280px}
.news-note{font-size:11.5px;margin-bottom:12px}
.news-input{width:232px;height:30px;background:var(--white);color:#999;font-size:11px;padding:7px 10px}
.news-submit{margin-top:14px;width:120px;height:32px;background:#e0506a;font-size:12px;font-weight:600;display:flex;align-items:center;justify-content:center;letter-spacing:1px}
.socials{display:flex;gap:8px}
.socials span{width:24px;height:24px;border-radius:50%;background:#e85a70}
.contact-row{display:flex;gap:8px;align-items:flex-start;font-size:11.5px;line-height:22px}
.contact-row svg{margin-top:6px;flex:none}
.footer-bar{position:absolute;top:2460px;left:0;width:1200px;height:48px;background:var(--red-deep);color:var(--white);font-size:11px;display:flex;align-items:center;justify-content:center;letter-spacing:.5px}
</style>
</head>
<body>
<header class="site-header">
  <div class="brand"><span class="brand-mark"></span>Fernlow Bails Inc</div>
  <nav class="main-nav">
    <a class="active" href="#">HOME</a>
    <a href="#">ABOUT US</a>
    <a href="#">WHAT WE OFFER</a>
    <a href="#">OUR SERVICE AREA</a>
    <a href="#">CONTACT US</a>
  </nav>
</header>

<section class="hero" role="img" aria-label="Photo of a hand holding jail keys in front of a prisoner behind bars">
  <div class="hero-text">
    <h2>WE BRING FAMILIES TOGETHER</h2>
    <p>Your Freedom Starts with Fernlow!</p>
    <p>Fernlow gets you out. Fernlow gets you home.</p>
    <p>We guarantee your bail</p>
  </div>
  <div class="slider-controls">
    <span class="slider-btn"><svg width="12" height="12" viewBox="0 0 12 12"><path d="M8 2 4 6l4 4" fill="none" stroke="#777" stroke-width="1.5"/></svg></span>
    <span class="slider-btn"><svg width="12" height="12" viewBox="0 0 12 12"><path d="m4 2 4 4-4 4" fill="none" stroke="#777" stroke-width="1.5"/></svg></span>
  </div>
</section>

<section class="about">
  <h2 class="section-title">ABOUT US</h2>
  <div class="title-rule"></div>
  <p class="about-lead">At Fernlow Bails, getting your loved one out of jail very quickly is our priority.</p>
  <p class="about-body">Fernlow Bails has been helping families across the region reunite with their loved ones since day one. Our licensed agents are available around the clock to explain every step, answer your questions and post bail quickly. We work with courts, jails and attorneys so you can focus on what matters most: bringing your family member home safely and as soon as possible.</p>
  <a class="btn" href="#">READ MORE</a>
</section>

<div class="divider"></div>

<section class="offer">
  <h2 class="section-title">WHAT WE OFFER</h2>
  <div class="title-rule"></div>
  <p class="offer-intro">At Fernlow Bails, we deal with:</p>
  <ul class="offer-list">
    <li class="offer-item">
      <div class="offer-icon"><svg width="70" height="50" viewBox="0 0 70 50" fill="none" stroke="#c8102e" stroke-width="5"><circle cx="18" cy="28" r="13"/><circle cx="52" cy="28" r="13"/><path d="M28 18c4-6 10-6 14 0"/></svg></div>
      <span class="offer-label">FELONY BAILS</span>
    </li>
    <li class="offer-item">
      <div class="offer-icon"><svg width="64" height="64" viewBox="0 0 64 64" fill="#c8102e"><rect x="16" y="8" width="30" height="14" rx="3" transform="rotate(-40 31 15)"/><rect x="26" y="22" width="6" height="34" rx="3" transform="rotate(-40 29 39)"/><rect x="6" y="54" width="36" height="6" rx="2"/></svg></div>
      <span class="offer-label">DRUG CHARGES BAILS</span>
    </li>
    <li class="offer-item">
      <div class="offer-icon"><svg width="60" height="64" viewBox="0 0 60 64" fill="#c8102e"><circle cx="16" cy="8" r="7"/><circle cx="44" cy="8" r="7"/><rect x="8" y="18" width="16" height="26" rx="3"/><rect x="10" y="40" width="5" height="22"/><rect x="17" y="40" width="5" height="22"/><path d="M44 18 56 46H32z"/><rect x="38" y="44" width="5" height="18"/><rect x="45" y="44" width="5" height="18"/></svg></div>
      <span class="offer-label">SEX CRIME BAILS</span>
    </li>
    <li class="offer-item">
      <div class="offer-icon"><svg width="64" height="64" viewBox="0 0 64 64" fill="#c8102e"><rect x="8" y="22" width="40" height="18" rx="9" transform="rotate(-40 28 31)"/><circle cx="44" cy="44" r="13"/><rect x="34" y="42" width="20" height="4" fill="#fff"/></svg></div>
      <span class="offer-label">DUI BAILS</span>
    </li>
    <li class="offer-item">
      <div class="offer-icon"><svg width="60" height="64" viewBox="0 0 60 64" fill="none" stroke="#c8102e" stroke-width="6" stroke-linecap="round"><circle cx="38" cy="8" r="6" fill="#c8102e" stroke="none"/><path d="M34 20 26 38l14 8-4 14M26 38l-10 20M14 28l12-8 14 6 8-6"/></svg></div>
      <span class="offer-label">THEFT BAILS</span>
    </li>
  </ul>
  <a class="btn" href="#">24/7 NOTARY PUBLIC SERVICE</a>
</section>

<section class="service-area" role="img" aria-label="Photo of handcuffed hands">
  <h2 class="section-title">OUR SERVICE AREA</h2>
  <div class="title-rule"></div>
  <p class="service-text">At Fernlow, our process is fast,<br>professional and effective.</p>
</section>

<footer class="site-footer">
  <div class="footer-col col-links">
    <h4>QUICK LINKS</h4>
    <ul><li>Home</li><li>About Us</li><li>What We Offer</li><li>Our Service Area</li><li>Contact Us</li></ul>
  </div>
  <div class="footer-col col-news">
    <h4>NEWS LETTER SIGNUP</h4>
    <p class="news-note">Sign up to be notified about news</p>
    <div class="news-input">Your Email</div>
    <div class="news-submit">SUBMIT</div>
  </div>
  <div class="footer-col col-follow">
    <h4>FOLLOW US</h4>
    <div class="socials"><span></span><span></span><span></span><span></span><span></span><span></span></div>
  </div>
  <div class="footer-col col-contact">
    <h4>CONTACT US</h4>
    <div class="contact-row"><svg width="10" height="10"><circle cx="5" cy="5" r="4" fill="#fff"/></svg><span><b>Office:</b> 412 Harlow Ave, Suite 9,<br>Brenton, NY 10000</span></div>
    <div class="contact-row"><svg width="10" height="10"><circle cx="5" cy="5" r="4" fill="#fff"/></svg><span><b>Mobile:</b> 555-014-2288</span></div>
    <div class="contact-row"><svg width="10" height="10"><circle cx="5" cy="5" r="4" fill="#fff"/></svg><span><b>Fax:</b> 555-014-2299</span></div>
    <div class="contact-row"><svg width="10" height="10"><circle cx="5" cy="5" r="4" fill="#fff"/></svg><span><b>Mail:</b> info@fernlowbails.com</span></div>
  </div>
</footer>
<div class="footer-bar">FERNLOW BAILS INC. © 2016 | Privacy Policy</div>
</body>
</html>
```